Vektordesign (AI) für Fensterfolien - Fenstertattoos
Zielgruppe
Wir betreiben einen Onlineshop für Fensterfolien. Unsere Fenstertattoos werden auf einem Schneideplotter auf die individuellen Maße des Kunden angefertigt. Dazu nutzen wir Vektordateien aus dem Adobe Illustrator.
Unseren Shop finden Sie unter: www.klebe-und-form.de
Aufgabenstellung
Es sollen Illustrator Vektorgrafiken erstellt werden, welche durch uns als Datei für die spätere Fertigung der Fensterfolien genutzt werden können.
Wir sind sehr interessiert unser Portfolio stark zu erweitern und wollen eine größere Zahl an Designs einkaufen. Bitte bieten Sie die Designs im 4er bis 5er Set an so das der Preis immer für 4 bis 5 Designs gilt.
Wichtig ist das die Motive nicht zu filigran werden. Was machbar ist sehen Sie auf unserer Internetseite. Sie sollten nicht zu speziell sein und eine große Käuferschicht ansprechen können. Die stärksten Kategorien sind dabei Badezimmer, Küche und Wohnzimmer. Moderne , schlichte und zeitgemäße, gerne auch florale Motive sind ideal.
Auch Motive für bestimmte Gewerbebetribe sind gewünscht. Z.B.

```html
<!DOCTYPE html>
<html lang="en">
<head>
<meta charset="utf-8">
<title>Kitchen Window Film</title>
<link rel="stylesheet" href="https://fonts.googleapis.com/css2?family=Anton&display=swap">
<style>
  :root {
    --backdrop: #56704c;
    --frost: #e7ede2;
    --motif-tone: #b7c7ae;
    --canvas-w: 1191px;
    --canvas-h: 1200px;
  }
  html, body {
    margin: 0;
    padding: 0;
    width: var(--canvas-w);
    height: var(--canvas-h);
    overflow: hidden;
    background: var(--backdrop);
  }
  .window-film {
    position: absolute;
    left: 0;
    top: 253px;
    width: var(--canvas-w);
    height: 694px;
    display: block;
  }
  .film-surface { fill: var(--frost); }
  .motif-area { fill: var(--motif-tone); }
  .cutout-text {
    font-family: "Anton", "Oswald", sans-serif;
    font-size: 207px;
  }
</style>
</head>
<body>
<svg class="window-film" viewBox="0 0 1555 905" xmlns="http://www.w3.org/2000/svg" aria-label="Frosted kitchen window film with the word KITCHEN">
  <defs>
    <mask id="film-cutouts" maskUnits="userSpaceOnUse" x="0" y="0" width="1555" height="905">
      <rect x="0" y="0" width="1555" height="905" fill="#fff"/>
      <text class="cutout-text" x="31" y="322" textLength="627" lengthAdjust="spacingAndGlyphs" fill="#000">KITCHEN</text>
    </mask>
  </defs>
  <g class="film-surface" mask="url(#film-cutouts)">
    <rect class="stripe-top" x="0" y="0" width="1555" height="15"/>
    <rect class="stripe-upper" x="0" y="50" width="1555" height="45"/>
    <rect class="band-title" x="0" y="130" width="1555" height="210"/>
    <rect class="band-main" x="0" y="400" width="1555" height="457"/>
    <rect class="stripe-bottom" x="0" y="866" width="1555" height="26"/>
  </g>
  <rect class="motif-area" x="551" y="422" width="510" height="435" role="img" aria-label="Cut-out motif of a steaming coffee cup"/>
</svg>
</body>
</html>
```